Tree Pruning Website

We need a website for a tree Arborist, pruning company called Maple Crest Canopy Works. We look after all types of trees, knock down trees and prune trees. Our target market is from domestic clients to government clients and everything in between.

We would like to see the use of our main colours which are orange and green

We are not looking forward in seeing a template that we have seen before but a unique template. We have designed 5 templates ourselves and we wish for the design community to take our designs to the next level.

We have also designed a template for things that **we are not** looking for (Version 4)

To make it fair for everyone, we are also not giving out any participation payments as we have had. One winner will take all of the payment!!!

I Have attached a image of the designs and a image of a tree.

We are just looking at the PSD file been developed. We have our own team who can slice the image up into a HTML format.

Target Market(s)

Everyone who needs to cut down a tree

Industry/Entity Type

Government

Requirements
Must have
• Logo on front page
A List of our services
jQuery slider on page
Phone Number on every page

```html
<!DOCTYPE html>
<html lang="en">
<head>
<meta charset="utf-8">
<title>Maple Crest Canopy Works</title>
<link href="https://fonts.googleapis.com/css2?family=Bree+Serif&family=Arimo:wght@400;700&display=swap" rel="stylesheet">
<style>
:root{
  --lime:#7fc31c;
  --lime-dark:#5f9a0c;
  --olive:#5c7a2e;
  --olive-dark:#3f5824;
  --orange:#f5a313;
  --orange-light:#ffc53a;
  --orange-text:#e08c00;
  --ink:#4a4a4a;
  --heading:#2f3d1f;
  --page:#efefef;
  --panel:#ffffff;
  --rule:#d9d9d9;
}
*{box-sizing:border-box;margin:0;padding:0}
html,body{width:1010px;height:1200px;overflow:hidden}
body{background:var(--page);font-family:'Arimo',Arial,sans-serif;color:var(--ink);position:relative}
.serif{font-family:'Bree Serif',Georgia,serif}

.site-header{position:absolute;left:0;top:0;width:1010px;height:65px;background:var(--lime)}
.brand{position:absolute;left:123px;top:6px;display:flex;align-items:center;gap:12px}
.brand-mark{width:52px;height:52px;border-radius:50%;background:#fff}
.brand-name{font-family:'Bree Serif',Georgia,serif;color:#fff;font-size:23px;line-height:25px}
.main-nav{position:absolute;left:463px;top:0;display:flex;height:65px}
.main-nav a{color:#fff;text-decoration:none;font-size:12px;font-weight:700;line-height:65px;padding:0 22px}
.main-nav a.active{background:var(--lime-dark);padding:0 21px}

.hero{position:absolute;left:0;top:65px;width:1010px;height:365px;background:linear-gradient(180deg,#8c8a4a 0%,#6f6132 35%,#7a5128 70%,#4d3a1f 100%)}
.hero-arrow{position:absolute;top:143px;width:30px;height:30px}

.content{position:absolute;left:104px;top:391px;width:803px;height:582px;background:var(--panel);border-top:3px solid var(--orange);box-shadow:0 0 6px rgba(0,0,0,.12)}
.intro{height:85px;background:#f7f7f7;border-bottom:1px solid var(--rule);position:relative}
.intro p{position:absolute;left:19px;top:20px;width:620px;font-family:'Bree Serif',Georgia,serif;font-size:18.5px;line-height:22px;color:#555}
.intro em{font-style:normal;color:var(--orange-text)}
.quote-btn{position:absolute;right:20px;top:20px;width:123px;height:40px;border-radius:3px;background:linear-gradient(var(--orange-light),var(--orange));color:#fff;font-family:'Bree Serif',Georgia,serif;font-size:16px;line-height:40px;text-align:center;box-shadow:0 2px 0 #d98400}

.services{position:absolute;left:0;top:85px;width:803px;height:156px;display:flex;padding:28px 0 0 19px;border-bottom:1px dashed var(--rule)}
.service{display:flex;width:192px}
.service-icon{width:48px;height:48px;border-radius:50%;background:#eef3e2;border:5px solid #e2ecd0;flex:none}
.service-body{margin-left:12px;width:118px}
.service h3{font-family:'Bree Serif',Georgia,serif;font-weight:400;font-size:17px;color:var(--heading);margin:-2px 0 5px}
.service p{font-size:10px;line-height:13px;text-align:justify;color:#333}

.testimonials{position:absolute;left:0;top:241px;width:803px;height:117px;background:#fafafa;border-bottom:1px dashed var(--rule)}
.t-arrow{position:absolute;top:43px;width:32px;height:32px}
.testimonial{position:absolute;top:20px;display:flex}
.avatar{width:80px;height:80px;flex:none}
.t-body{margin-left:28px;width:225px}
.t-body p{font-size:10px;line-height:13px;color:#777}
.t-meta{display:flex;align-items:center;gap:12px;margin-top:8px}
.t-name{background:var(--orange-light);color:#fff;font-size:9.5px;padding:3px 10px;border-radius:2px}
.t-name b{font-weight:700}

.gallery{position:absolute;left:19px;top:380px;display:flex;gap:20px}
.gallery div{width:243px;height:178px}

.newsletter{position:absolute;left:0;top:973px;width:1010px;height:83px;background:var(--olive)}
.nl-at{position:absolute;left:138px;top:6px;font-family:'Bree Serif',Georgia,serif;font-size:58px;color:var(--lime);line-height:70px}
.nl-title{position:absolute;left:202px;top:18px;font-family:'Bree Serif',Georgia,serif;color:#fff;font-size:21px}
.nl-sub{position:absolute;left:203px;top:46px;color:#fff;font-size:10px}
.nl-input{position:absolute;top:26px;height:33px;background:#fff;border:4px solid #97b85a;border-radius:3px;font-size:10.5px;color:#666;line-height:25px;padding-left:10px}
.nl-btn{position:absolute;left:781px;top:26px;width:110px;height:33px;background:linear-gradient(var(--orange-light),var(--orange));border-radius:3px;font-family:'Bree Serif',Georgia,serif;color:var(--heading);font-size:14px;line-height:33px;text-align:center}

.site-footer{position:absolute;left:0;top:1056px;width:1010px;height:144px;background:var(--olive-dark)}
.f-col{position:absolute;top:12px;color:#fff}
.f-col h4{font-family:'Bree Serif',Georgia,serif;font-weight:400;font-size:18px;margin-bottom:12px}
.f-col p,.f-col li{font-family:'Bree Serif',Georgia,serif;font-size:11px;line-height:15px;list-style:none}
.clients{display:flex;gap:24px;margin-top:30px;font-size:13px;font-weight:700;font-family:'Arimo',Arial,sans-serif}
.f-brand{position:absolute;left:723px;top:14px;display:flex;align-items:center;gap:8px}
.f-brand span{font-family:'Bree Serif',Georgia,serif;color:#fff;font-size:19px;line-height:21px}
.f-brand i{width:36px;height:36px;border-radius:50%;background:#fff;display:block}
.f-legal{position:absolute;right:144px;top:69px;text-align:right;color:#fff;font-size:9px;line-height:14px}
.social{position:absolute;left:798px;top:106px;display:flex;gap:7px}
.social i{width:20px;height:20px;border-radius:50%;background:#6b7d4f;border:1px solid #8a9a6e;display:block}
</style>
</head>
<body>

<header class="site-header">
  <div class="brand"><span class="brand-mark"></span><span class="brand-name">Maple Crest<br>Canopy Works</span></div>
  <nav class="main-nav">
    <a class="active" href="#">Home</a><a href="#">About Us</a><a href="#">Our Services</a><a href="#">Get a Quote</a><a href="#">Contact Us</a>
  </nav>
</header>

<section class="hero" role="img" aria-label="Slider photo of a woodland path lined with autumn birch trees and ferns">
  <svg class="hero-arrow" style="left:112px" viewBox="0 0 30 30"><circle cx="15" cy="15" r="15" fill="#fff"/><path d="M17 9l-6 6 6 6" stroke="#333" stroke-width="2.5" fill="none"/></svg>
  <svg class="hero-arrow" style="left:868px" viewBox="0 0 30 30"><circle cx="15" cy="15" r="15" fill="#fff"/><path d="M13 9l6 6-6 6" stroke="#333" stroke-width="2.5" fill="none"/></svg>
</section>

<main class="content">
  <div class="intro">
    <p>Maple Crest is the leading tree pruning services located in perth. Our motto is when you call, we <em>gurrantee</em> to turn up and <em>provide care</em> to our customers.</p>
    <div class="quote-btn">Get a QUOTE!</div>
  </div>

  <section class="services">
    <div class="service"><div class="service-icon"></div><div class="service-body"><h3>Domestic</h3><p>Lorem Ipsum is simply dummy text of the printing and typesetting industry. Lorem Ipsum has been.</p></div></div>
    <div class="service"><div class="service-icon"></div><div class="service-body"><h3>Commercial</h3><p>Lorem Ipsum is simply dummy text of the printing and typesetting industry. Lorem Ipsum has been.</p></div></div>
    <div class="service"><div class="service-icon"></div><div class="service-body"><h3>Link Management</h3><p>Lorem Ipsum is simply dummy text of the printing and typesetting industry. Lorem Ipsum has been.</p></div></div>
    <div class="service"><div class="service-icon"></div><div class="service-body"><h3>Non Profit</h3><p>Lorem Ipsum is simply dummy text of the printing and typesetting industry. Lorem Ipsum has been.</p></div></div>
  </section>

  <section class="testimonials">
    <svg class="t-arrow" style="left:-6px" viewBox="0 0 32 32"><circle cx="16" cy="16" r="15" fill="#fff" stroke="#cfe0b4" stroke-width="2"/><path d="M18 10l-6 6 6 6" stroke="#9bbf66" stroke-width="2.5" fill="none"/></svg>
    <div class="testimonial" style="left:44px">
      <svg class="avatar" viewBox="0 0 80 80" role="img" aria-label="Customer portrait"><rect x="14" y="14" width="52" height="52" transform="rotate(45 40 40)" fill="#c9a27e" stroke="#ffc53a" stroke-width="4"/></svg>
      <div class="t-body"><p>It is a long established fact that a reader will be distracted by the readable content of a page when looking at its layout.</p>
        <div class="t-meta"><span class="t-name"><b>Sam,</b> Garden Journal</span><svg width="78" height="13" viewBox="0 0 78 13"><g fill="#ffc500"><path id="st" d="M6.5 0l1.9 4.3 4.6.4-3.5 3 1.1 4.6-4.1-2.5-4.1 2.5 1.1-4.6-3.5-3 4.6-.4z"/><use href="#st" x="16"/><use href="#st" x="32"/><use href="#st" x="48"/><use href="#st" x="64"/></g></svg></div></div>
    </div>
    <div class="testimonial" style="left:387px">
      <svg class="avatar" viewBox="0 0 80 80" role="img" aria-label="Customer portrait"><rect x="14" y="14" width="52" height="52" transform="rotate(45 40 40)" fill="#b88a6a" stroke="#ffc53a" stroke-width="4"/></svg>
      <div class="t-body"><p>It is a long established fact that a reader will be distracted by the readable content of a page when looking at its layout.</p>
        <div class="t-meta"><span class="t-name"><b>Sam,</b> Garden Journal</span><svg width="78" height="13" viewBox="0 0 78 13"><g fill="#ffc500"><use href="#st"/><use href="#st" x="16"/><use href="#st" x="32"/><use href="#st" x="48"/><use href="#st" x="64"/></g></svg></div></div>
    </div>
    <svg class="t-arrow" style="left:754px" viewBox="0 0 32 32"><circle cx="16" cy="16" r="15" fill="#fff" stroke="#cfe0b4" stroke-width="2"/><path d="M14 10l6 6-6 6" stroke="#9bbf66" stroke-width="2.5" fill="none"/></svg>
  </section>

  <section class="gallery">
    <div role="img" aria-label="Photo of an avenue of green trees over a lawn" style="background:linear-gradient(180deg,#4f8a2a,#2f5a1a 60%,#6fc63a)"></div>
    <div role="img" aria-label="Photo of spring trees above a bed of red and orange tulips" style="background:linear-gradient(180deg,#8fbf3a,#5f8f2a 55%,#e0521c 80%,#f0a020)"></div>
    <div role="img" aria-label="Photo of a shaded park walkway under tall trees" style="background:linear-gradient(180deg,#3f7a2a,#2a4a1f 60%,#7a8a70)"></div>
  </section>
</main>

<section class="newsletter">
  <div class="nl-at">@</div>
  <div class="nl-title">Newsletter</div>
  <div class="nl-sub">Lorem Ipsum is simply dummy text</div>
  <div class="nl-input" style="left:399px;width:183px">Your name</div>
  <div class="nl-input" style="left:593px;width:175px">Your email address</div>
  <div class="nl-btn">SUBSCRIBE</div>
</section>

<footer class="site-footer">
  <div class="f-col" style="left:134px"><h4>Contact Us</h4><p>48 Fernhill Road<br>BRAMBLETON, WA 6099</p><p style="margin-top:14px">Phone : 08 5550 1420<br>Fax: 08 5550 1421</p></div>
  <div class="f-col" style="left:297px"><h4>Our Clients</h4><div class="clients"><span>Verdant Co</span><span>Leafline</span></div></div>
  <div class="f-col" style="left:496px"><h4>Site map</h4><ul><li>Dangerous Tree Removal</li><li>Stump Removal</li><li>Tree Trimming</li><li>Tree Shapping</li></ul></div>
  <div class="f-brand"><span>Maple Crest<br>Canopy Works</span><i></i></div>
  <div class="f-legal">© 2013 maple crest canopy works.All right Reaerved.<br>Site design by Birchway Studio</div>
  <div class="social"><i></i><i></i><i></i></div>
</footer>

</body>
</html>
```